Rice Cakes Packing Desing

We need a simple (4 color) yet colorful, atractive design for a Rice Cake polypropylene bag. We are expanding our line to include 8-10 different flavors with each bag being a different color for easy identificaction. We are starting right with the first design. We already have "sample model" (of an existing product in the usa market) upon which we believe that our design could be based on (as an idea of a simple 4 color plastic bag design), which we are including in this post. We are also including an image of Brindle Rice Cakes plastic bag that has a round front window that shows the product inside the bag, which we also would like to include in our design. We already have a brand name and a logo design. The bag's dimension is about 20cms (wide) 30cms (tall) and it will contain about 12 rice cakes inside. (I HAVE ATTACHED A COUPLE OF IMAGES OF A PRINTED POLYPROPYLENE RICE CAKES BAG FOR YOUR REFERENCE)
Updates

Project Deadline Extended
Reason: We want to provide the designers with NUTRITIONAL INFORMATION, Bar Code, Company information, Ingredients, important pointers, etc. to be incorporated into the design. We would like to provide a few more days in order to fully integrate the back & front text into the package design in order to attain a perfectly balanced and well presented package. So far we have received some very interesting and highly viable proposals and we would like to provide the designers the necessary text information in order to have a complete, fully designed, great-looking package. We feel that with the extension the final design can be completed and we can have an opportunity to review, incorporate/change/modify any details before choosing the final design. Great designs have been submitted and we will definitely choose one before the newly proposed deadline. Thanks to all!

Target Market(s)

Although the concept of RICE CAKES might very well have its origins in ASIA the idea is to create a design (logo & pack) that will convey a message to the end consumer that our brand name stands for "FRESHNESS", "HEALTHY", "NATURE'S BEST", "TOP GRAINS", "GOODNESS", in short if you consume are products "IT IS GOOD FOR YOU!" (not only for people who love oriental food). We would like to have a product image that says "Hey! This looks Healthy & Tasty" (non-fattening, yummy and good!)

When you buy a pack of GRANOLAS what do you think about? What do you believe it is that you are buying? Good, Healthy Stuff? Good Tasting? Good for you? That's the idea!

Besides Rice Cakes are super light, fluffy, crunchy and easy to digest that it makes it a great Snack for everyone! Kids & Adults!

We need the full complete design of the actual bag (where the Rice Cakes will be packed) in order to start production of the bags right.

Industry/Entity Type

Plastic

Requirements
Must have
• We already have a local company in Mexico City that makes printed polypropylene bags. They are only waiting for the bag design in order to print the 20cms x 30cms bags.
Kindly consider that on the back Nutritional Information will be needed as well as a BarCode, company information, some bullets (pointing to the most important benefits of the product), etc. We will provide all the text information.
Nice to have
• Kindly take a look at the newly uploaded images from "TORVE" Rice Cake packages. They are a good example of how to accomplish a great looking design using only 4 colors (which saves a lot in printing costs)
Should not have
• We do NOT want to have a design that says "This is ORIENTAL food". We don't want it to appear like "Sushi Rice" or "Japanese food", etc.

```html
<!DOCTYPE html>
<html lang="en">
<head>
<meta charset="utf-8">
<title>Rice Cakes Bag Fronts</title>
<link href="https://fonts.googleapis.com/css2?family=Oswald:wght@400;500&family=Gelasio:wght@400&family=Lato:ital,wght@0,700;1,400&display=swap" rel="stylesheet">
<style>
  :root {
    --page: #f3f1ee;
    --brown: #8a6a3f;
    --brown-dark: #6f5430;
    --white: #ffffff;
    --salted: #4cc0e2;
    --salted-soft: #8fd8ef;
    --salted-deep: #2e9fc6;
    --cinnamon: #e0692c;
    --cinnamon-soft: #f09a66;
    --cinnamon-deep: #b9461a;
  }
  * { box-sizing: border-box; margin: 0; padding: 0; }
  html, body { width: 1200px; height: 777px; overflow: hidden; background: var(--page); }
  .canvas { position: relative; width: 1200px; height: 777px; }

  .bag { position: absolute; top: 40px; width: 240px; height: 700px; }
  .bag--salted { left: 300px; --tone: var(--salted); --tone-soft: var(--salted-soft); --tone-deep: var(--salted-deep); }
  .bag--cinnamon { left: 660px; --tone: var(--cinnamon); --tone-soft: var(--cinnamon-soft); --tone-deep: var(--cinnamon-deep); }

  .bag__tie { position: absolute; top: 0; left: 0; width: 240px; height: 170px; }
  .bag__body {
    position: absolute; top: 165px; left: 0; width: 240px; height: 530px;
    background: var(--tone); border-radius: 26px 26px 14px 14px; overflow: hidden;
  }
  .bag__pattern {
    position: absolute; top: 0; left: 0; width: 100%; height: 120px;
    background: linear-gradient(180deg, var(--tone-soft) 0%, var(--tone) 100%);
  }
  .bag__band {
    position: absolute; top: 115px; left: 0; width: 100%; height: 128px;
    background: var(--brown); text-align: center; color: var(--white);
  }
  .brand-badge {
    position: absolute; top: 62px; left: 82px; width: 76px; height: 76px;
    border-radius: 50%; background: var(--white); border: 3px solid var(--brown-dark);
  }
  .brand-name {
    position: absolute; top: 146px; width: 100%; text-align: center;
    font-family: "Lato", sans-serif; font-weight: 700; font-size: 10px; letter-spacing: 0.5px; color: var(--white);
  }
  .product-title {
    position: absolute; top: 160px; width: 100%; text-align: center;
    font-family: "Oswald", sans-serif; font-weight: 400; font-size: 48px; line-height: 1; color: var(--white); letter-spacing: 0.5px;
  }
  .product-tagline {
    position: absolute; top: 220px; width: 100%; text-align: center;
    font-family: "Lato", sans-serif; font-style: italic; font-size: 12px; color: var(--white);
  }
  .bag__strip {
    position: absolute; top: 243px; left: 0; width: 42px; height: 287px;
    background: linear-gradient(180deg, var(--tone-soft), #f4ead6 50%, var(--tone-soft));
    opacity: 0.85;
  }
  .flavor {
    position: absolute; top: 262px; left: 62px;
    font-family: "Gelasio", serif; font-size: 29px; color: var(--white); line-height: 1;
  }
  .benefits {
    position: absolute; top: 308px; left: 64px; list-style: none;
    font-family: "Gelasio", serif; font-size: 10.5px; color: var(--white); line-height: 1.55;
  }
  .benefits li::before { content: "\25CF"; font-size: 7px; margin-right: 6px; vertical-align: 2px; }
  .product-photo {
    position: absolute; left: 84px; top: 370px; width: 146px; height: 140px; border-radius: 50%;
  }
  .bag--salted .product-photo { background: radial-gradient(circle at 45% 55%, #f6f1e3 0%, #e6dcc2 55%, var(--tone) 75%); }
  .bag--cinnamon .product-photo { background: radial-gradient(circle at 50% 50%, #9a4a22 0%, #7a3515 50%, var(--tone) 75%); }
</style>
</head>
<body>
<main class="canvas">

  <article class="bag bag--salted">
    <svg class="bag__tie" viewBox="0 0 240 170" aria-hidden="true">
      <path d="M70 10 C90 30 100 40 108 150 L132 150 C140 40 150 30 172 8 C150 20 140 28 120 20 C100 30 90 22 70 10 Z" fill="var(--salted-deep)"/>
      <rect x="104" y="135" width="32" height="18" fill="var(--white)"/>
      <path d="M104 153 L136 153 L200 175 L40 175 Z" fill="var(--salted)"/>
    </svg>
    <div class="bag__body">
      <div class="bag__pattern" role="img" aria-label="Faint wheat stalk pattern"></div>
      <div class="bag__band"></div>
      <div class="brand-badge" role="img" aria-label="Brand badge"></div>
      <p class="brand-name">OLVEN FOODS</p>
      <h2 class="product-title">RICE CAKES</h2>
      <p class="product-tagline">Healthy &amp; Tasty Rice Snack</p>
      <div class="bag__strip" role="img" aria-label="Column of rice cake pictures"></div>
      <p class="flavor">lightly salted</p>
      <ul class="benefits">
        <li>No Preservatives</li>
        <li>Gluten Free</li>
        <li>Low Calories</li>
      </ul>
      <div class="product-photo" role="img" aria-label="Photo of rice cakes with a salt shaker"></div>
    </div>
  </article>

  <article class="bag bag--cinnamon">
    <svg class="bag__tie" viewBox="0 0 240 170" aria-hidden="true">
      <path d="M70 10 C90 30 100 40 108 150 L132 150 C140 40 150 30 172 8 C150 20 140 28 120 20 C100 30 90 22 70 10 Z" fill="var(--cinnamon-deep)"/>
      <rect x="104" y="135" width="32" height="18" fill="var(--white)"/>
      <path d="M104 153 L136 153 L200 175 L40 175 Z" fill="var(--cinnamon)"/>
    </svg>
    <div class="bag__body">
      <div class="bag__pattern" role="img" aria-label="Faint wheat stalk pattern"></div>
      <div class="bag__band"></div>
      <div class="brand-badge" role="img" aria-label="Brand badge"></div>
      <p class="brand-name">OLVEN FOODS</p>
      <h2 class="product-title">RICE CAKES</h2>
      <p class="product-tagline">Healthy &amp; Tasty Rice Snack</p>
      <div class="bag__strip" role="img" aria-label="Column of rice cake pictures"></div>
      <p class="flavor">cinnamon</p>
      <ul class="benefits">
        <li>No Preservatives</li>
        <li>Gluten Free</li>
        <li>Low Calories</li>
      </ul>
      <div class="product-photo" role="img" aria-label="Photo of cinnamon sticks"></div>
    </div>
  </article>

</main>
</body>
</html>
```